Church Website with Home Page and Member Sermon Library

I am in need of an updated design for our church website. This will include 4 pages (outlined below). We are a conservative, evangelical, Christian church. The site should be modern and clean, while still reflecting our conservative values. I already have a logo for our church, and I want the site to incorporate the logo, and match the logo/branding. Stock photos are allowed if needed, but I have uploaded some images of our church and would prefer those images to be used if possible. Any stock photos used should not include any people in the photos (scenery, nature, buildings, animals, etc. are fine).

The site will need 4 pages: Home, Support Us (Donate), Login, and Recording Library.

Page 1: Home
The home page should include the following sections:

- Navigation: Should include links to each section of the home page plus a "listen live" link which will take the user to a live-streaming site and a "support us" link which will take the user to a support/donate page.

- Announcements: Can be either a banner or some other design, but there needs to be some way for us to post announcements for visitors to see. I'm open for creative ideas in this section, but would like it not to take up a lot of room on the page.

- About Us: Should include address, service times (see attached document), and information about the church.

- Pastor Bio: A section that introduces our pastor and gives a short bio about our pastor. Would like this section to include a picture of our pastor. Somewhere in this section I would like to include this Bible reference: "And I will give you pastors according to mine heart, which shall feed you with knowledge and understanding. Jer 3:15 LPW"

- Articles of Faith (What We Believe): This should include several sub-sections each with a heading, body, and possibly 1 or more scripture references. I have attached a document to the brief that includes our articles of faith. Feel free to be creative with this section in how you lay these out and format them.

- Support Us: A small section that explains what kind of support someone can give and a link to a donation page. The link can say something like "Support Us" or "Donate Now".

- Contact form: A contact form that allows the visitor to send us a message. The contact form should ask for name, email, phone, and message.

- Footer: A footer that will be displayed on all pages of the site. This should include at a minimum a link to the home page (or a link to each individual section in the home page if you prefer), a link to "listen live", a link to "support us", a link to "contact us" (or you can put the contact form directly in the footer if you prefer), the address, and a "member login" link.

Page 2: Support Us
The donation page should include a form the visitor can fill out to make a donation. We will embed a third party form later. For this design, please just mock out the design with a basic form asking for name, phone, and email.

Page 3: Login
The recording library (detailed below) will require members to login with a shared numeric code before accessing the page. We need a design for a login screen. The screen should include navigation/footer just like all other pages, but the body of the login page will consist only of a form that asks the user to enter the access code and then a "login" button.

Page 4: Recording Library

The library page is a member-only page that will require a shared, numeric pass code to access. On this page, members will be able to access a filterable list of past sermons. The page by default should display most recent sermons, but should also include a search form that allows the member to filter the sermon list to find a particular sermon. The search form should allow the user to select a filter type (e.g. Speaker name, date, event, etc.) and type in a value to search. They should be able to add multiple filters and remove filters that have been added. Each sermon that is displayed in the result list should include basic information such as title, date, speaker, tags, etc. along with a download icon, and an embedded audio player where they can click a play button to stream it on-demand. Each sermon should also have clickable tags associated with it that can be used to find related sermons.
Updates

I have uploaded several images of our church. Feel free to incorporate these into your design if possible.

Target Market(s)

Church Members

Industry/Entity Type

Religion

Number of Pages Required

4 page

Font styles to use
Sans Serif

Colors

Designer to choose colors to be used in the design.

Requirements
Must have
• Must incorporate the logo (attached)
Nice to have
• Would like the design to incorporate pictures of our church (attached) instead of stock photos if possible.
Should not have
• Please avoid an overly cluttered design. Stock photos used should not include any people in the photos.

```html
<!DOCTYPE html>
<html lang="en">
<head>
<meta charset="utf-8">
<title>Grace Covenant Chapel — Articles of Faith</title>
<link rel="stylesheet" href="https://fonts.googleapis.com/css2?family=Inter:wght@400;500;600;700&family=Marcellus&display=swap">
<style>
  :root {
    --paper: #e0dbd1;
    --paper-deep: #d6d0c4;
    --sage: #62874f;
    --forest: #2b4a1f;
    --ink: #1b1b1b;
    --white: #ffffff;
    --teal: #1a8fb0;
    --card-light: #efefee;
  }
  * { box-sizing: border-box; margin: 0; padding: 0; }
  html, body { width: 736px; height: 1200px; overflow: hidden; }
  body {
    position: relative;
    background: linear-gradient(180deg, var(--paper) 0%, var(--paper) 55%, var(--paper-deep) 100%);
    font-family: "Inter", sans-serif;
    color: var(--ink);
  }
  .abs { position: absolute; }

  /* Articles band */
  .faith-band { position: absolute; left: 0; top: 0; }
  .eyebrow {
    left: 0; width: 736px; top: 154px; text-align: center;
    font-family: "Marcellus", serif; font-size: 7.5px; letter-spacing: 2.2px; color: var(--white);
  }
  .section-title {
    left: 0; width: 736px; text-align: center;
    font-family: "Marcellus", serif; font-weight: 400;
  }
  .faith-title { top: 172px; font-size: 23px; color: var(--white); }

  .article { top: 217px; width: 160px; height: 255px; color: var(--white); }
  .article-photo { width: 160px; height: 145px; border-radius: 8px; }
  .article-tag { left: 6px; top: 158px; font-size: 6px; font-weight: 700; letter-spacing: .2px; }
  .article-name { left: 6px; top: 169px; font-size: 11.5px; font-weight: 600; line-height: 14px; white-space: nowrap; }
  .article-name.is-low { top: 171px; }
  .article-text { left: 6px; top: 192px; font-size: 6.8px; line-height: 10.8px; }
  .know-more { left: 6px; top: 243px; font-size: 6.2px; font-weight: 700; display: flex; align-items: center; gap: 4px; }

  .explore-btn {
    left: 329px; top: 508px; width: 78px; height: 25px; background: var(--white);
    border-radius: 2px; display: flex; align-items: center; justify-content: center; gap: 5px;
    font-size: 7.6px; font-weight: 500; color: var(--forest);
  }

  /* Announcements */
  .announce-title { top: 674px; font-size: 23px; color: var(--ink); }
  .notice { top: 730px; height: 130px; border-radius: 65px; overflow: hidden; }
  .notice-closed { left: 120px; width: 249px; background: var(--sage); color: var(--white); }
  .notice-change { left: 380px; width: 236px; background: var(--card-light); }
  .notice-art-closed {
    left: 29px; top: 18px; width: 107px; height: 90px; border-radius: 10px;
    background: linear-gradient(160deg, #f3efe6 0%, #e9b04a 55%, #2a2a2a 100%);
  }
  .notice-heading { left: 143px; top: 27px; font-size: 20px; font-weight: 700; line-height: 22px; }
  .notice-meta { left: 145px; font-size: 7px; font-weight: 500; display: flex; align-items: center; gap: 4px; white-space: nowrap; }
  .brand-mini { left: 24px; top: 20px; font-size: 5px; font-weight: 600; line-height: 6.5px; color: var(--ink); text-align: center; }
  .notice-kicker { left: 113px; top: 15px; font-size: 8px; font-weight: 500; color: var(--ink); white-space: nowrap; }
  .notice-art-change {
    left: 58px; top: 38px; width: 160px; height: 78px; border-radius: 8px;
    background: linear-gradient(100deg, #f6d23a 0%, #f07a1f 55%, #d9342b 100%);
  }

  /* Footer */
  .rule { left: 120px; width: 496px; height: 2px; border-radius: 2px;
    background: linear-gradient(90deg, rgba(26,143,176,0) 0%, var(--teal) 20%, var(--teal) 80%, rgba(26,143,176,0) 100%); }
  .brand-block { left: 0; width: 736px; top: 968px; text-align: center; font-family: "Marcellus", serif; color: var(--ink); }
  .brand-name { font-size: 18px; letter-spacing: 1.5px; line-height: 23px; }
  .contact-row { left: 127px; top: 1046px; display: flex; align-items: center; font-size: 6.6px; font-weight: 500; white-space: nowrap; }
  .contact-item { display: flex; align-items: center; gap: 3px; }
  .contact-sep { width: 1px; height: 12px; background: #bdb6a8; margin: 0 8px; }
  .visit-btn {
    left: 543px; top: 1045px; width: 73px; height: 25px; background: var(--forest); color: var(--white);
    border-radius: 2px; display: flex; align-items: center; justify-content: center; gap: 5px;
    font-size: 7.6px; font-weight: 500;
  }
  .social { top: 1110px; left: 315px; display: flex; gap: 6.5px; }
  .social-dot { width: 21px; height: 21px; border-radius: 50%; background: var(--teal); display: flex; align-items: center; justify-content: center; }
  .copyright { left: 0; width: 736px; top: 1146px; text-align: center; font-size: 6.9px; font-weight: 500; }
</style>
</head>
<body>

  <svg class="faith-band" width="736" height="620" viewBox="0 0 736 620" aria-hidden="true">
    <path fill="#62874f" d="M70 74 L368 89 L666 74 Q709 74 709 117 L709 569 Q709 612 666 612 L368 597 L70 612 Q27 612 27 569 L27 117 Q27 74 70 74 Z"/>
  </svg>

  <p class="abs eyebrow">DAILY ARTICLES</p>
  <h2 class="abs section-title faith-title">Articles of Faith</h2>

  <article class="abs article" style="left:120px">
    <div class="article-photo" role="img" aria-label="Gothic cathedral nave with rows of wooden chairs" style="background:linear-gradient(180deg,#8b7a62 0%,#5a4330 50%,#2a1610 100%)"></div>
    <p class="abs article-tag">EVENTS</p>
    <h3 class="abs article-name">The God Head</h3>
    <p class="abs article-text" style="width:132px">We believe in the God head bodily, known as the Divine Trinity. This body consist of God the father, Jesus Christ, his only begotten son and the.</p>
    <p class="abs know-more">Know More <svg width="5" height="7" viewBox="0 0 5 7"><path d="M1 1l2.5 2.5L1 6" stroke="#fff" stroke-width="1.2" fill="none"/></svg></p>
  </article>

  <article class="abs article" style="left:288px">
    <div class="article-photo" role="img" aria-label="Bright church interior with stone columns and wooden chairs" style="background:linear-gradient(180deg,#a08a70 0%,#b99a72 50%,#8a8e94 100%)"></div>
    <p class="abs article-tag" style="left:0">EVENTS</p>
    <h3 class="abs article-name is-low" style="left:0">Full Salvation.</h3>
    <p class="abs article-text" style="left:0;width:152px">We believe that Salvation is received only when a person comes to the realization that he or she is lost and separated from God and becomes full of godly sorrow.</p>
    <p class="abs know-more" style="left:0">Know More <svg width="5" height="7" viewBox="0 0 5 7"><path d="M1 1l2.5 2.5L1 6" stroke="#fff" stroke-width="1.2" fill="none"/></svg></p>
  </article>

  <article class="abs article" style="left:457px">
    <div class="article-photo" role="img" aria-label="Chapel interior with blue arches and wooden pews" style="background:linear-gradient(180deg,#8fa0ad 0%,#cfd3d0 35%,#6b5040 100%)"></div>
    <p class="abs article-tag" style="left:0">EVENTS</p>
    <h3 class="abs article-name is-low" style="left:0">Sanctification.</h3>
    <p class="abs article-text" style="left:0;width:160px">Printer took a galley of type and scrambled it to make a type specimen book. It has survived not only five centuries, but also the leap into.</p>
    <p class="abs know-more" style="left:0">Know More <svg width="5" height="7" viewBox="0 0 5 7"><path d="M1 1l2.5 2.5L1 6" stroke="#fff" stroke-width="1.2" fill="none"/></svg></p>
  </article>

  <a class="abs explore-btn">Explore More <svg width="5" height="7" viewBox="0 0 5 7"><path d="M1 1l2.5 2.5L1 6" stroke="#2b4a1f" stroke-width="1.2" fill="none"/></svg></a>

  <h2 class="abs section-title announce-title">Important Announcement</h2>

  <section class="abs notice notice-closed">
    <div class="abs notice-art-closed" role="img" aria-label="Megaphone announcement banner illustration"></div>
    <p class="abs notice-heading">Chruch<br>Closed</p>
    <p class="abs notice-meta" style="top:80px">
      <svg width="10" height="10" viewBox="0 0 10 10"><rect x="1" y="2" width="8" height="7" rx="1" fill="none" stroke="#fff" stroke-width=".8"/><path d="M1 4h8M3 1v2M7 1v2" stroke="#fff" stroke-width=".8"/></svg>
      Monday Friday
    </p>
    <p class="abs notice-meta" style="top:94px">9:00am - 5:30pm PST</p>
  </section>

  <section class="abs notice notice-change">
    <p class="abs brand-mini">GRACE<br>COVENANT<br>CHAPEL</p>
    <p class="abs notice-kicker">*Service time Change</p>
    <div class="abs notice-art-change" role="img" aria-label="Service time announcement banner with megaphone illustration"></div>
  </section>

  <div class="abs rule" style="top:909px"></div>

  <div class="abs brand-block">
    <p class="brand-name">GRACE COVENANT</p>
    <p class="brand-name">CHAPEL</p>
  </div>

  <div class="abs contact-row">
    <span class="contact-item">
      <svg width="7" height="7" viewBox="0 0 10 10"><path d="M2 1l2 2-1 1.5c.8 1.5 1.8 2.5 3.5 3.5L8 6l2 2-1.5 1.5C4.5 9 1 5.5.5 1.5Z" fill="#62874f"/></svg>
      +1 55501 24870
    </span>
    <span class="contact-sep"></span>
    <span class="contact-item">
      <svg width="7" height="6" viewBox="0 0 10 8"><rect width="10" height="8" rx="1" fill="#62874f"/><path d="M0.5 1l4.5 3.5L9.5 1" stroke="#e0dbd1" stroke-width=".9" fill="none"/></svg>
      office@gracecovenant.org
    </span>
  </div>

  <a class="abs visit-btn">Book a Visit <svg width="5" height="7" viewBox="0 0 5 7"><path d="M1 1l2.5 2.5L1 6" stroke="#fff" stroke-width="1.2" fill="none"/></svg></a>

  <div class="abs rule" style="top:1086px"></div>

  <nav class="abs social" aria-label="Follow and share">
    <a class="social-dot" aria-label="Share">
      <svg width="9" height="9" viewBox="0 0 10 10"><circle cx="2" cy="5" r="1.4" fill="#fff"/><circle cx="8" cy="2" r="1.4" fill="#fff"/><circle cx="8" cy="8" r="1.4" fill="#fff"/><path d="M2 5L8 2M2 5l6 3" stroke="#fff" stroke-width=".9"/></svg>
    </a>
    <a class="social-dot" aria-label="Website">
      <svg width="9" height="9" viewBox="0 0 10 10"><circle cx="5" cy="5" r="4" fill="none" stroke="#fff" stroke-width=".9"/><ellipse cx="5" cy="5" rx="1.8" ry="4" fill="none" stroke="#fff" stroke-width=".8"/><path d="M1 5h8" stroke="#fff" stroke-width=".8"/></svg>
    </a>
    <a class="social-dot" aria-label="Email">
      <svg width="9" height="7" viewBox="0 0 10 8"><rect x=".5" y=".5" width="9" height="7" rx="1" fill="none" stroke="#fff" stroke-width=".9"/><path d="M1 1l4 3.3L9 1" stroke="#fff" stroke-width=".9" fill="none"/></svg>
    </a>
    <a class="social-dot" aria-label="Listen live">
      <svg width="8" height="8" viewBox="0 0 10 10"><path d="M3 1.5v7l6-3.5z" fill="#fff"/></svg>
    </a>
  </nav>

  <p class="abs copyright">© Copyright Grace Covenant Chapel 2023. All Right Reserved.</p>

</body>
</html>
```